School Poster

Design so that these can be placed in classrooms across the school.

Attached is another design we have had done. Use a similar theme.

Consider using themes from https://corvalhs.edq.example.au/

please edit Binder1 doc.

Students and teachers

```html
<!DOCTYPE html>
<html lang="en">
<head>
<meta charset="utf-8">
<title>Corval State High School – Classroom Posters</title>
<link rel="stylesheet" href="https://fonts.googleapis.com/css2?family=Barlow+Condensed:wght@600;700&family=Montserrat:wght@400;500;600;700&family=Kaushan+Script&display=swap">
<style>
  :root{
    --navy:#061a3a;
    --navy-deep:#04132c;
    --yellow:#fdc20f;
    --yellow-soft:#f6e27a;
    --grey:#d9dce0;
    --white:#ffffff;
    --red:#e1141c;
    --head:"Barlow Condensed", "Arial Narrow", sans-serif;
    --body:"Montserrat", Arial, sans-serif;
    --script:"Kaushan Script", cursive;
  }
  *{box-sizing:border-box;margin:0;padding:0}
  html,body{width:1200px;height:847px;overflow:hidden;background:var(--white)}
  .canvas{position:relative;width:1200px;height:847px;overflow:hidden;background:var(--white);font-family:var(--body)}
  .abs{position:absolute}

  /* ---------- Poster shells ---------- */
  .poster{position:absolute;top:0;height:847px;overflow:hidden;background:var(--navy)}
  .poster--ai{left:0;width:592px;background:radial-gradient(ellipse 220px 160px at 340px 180px,#4b5f86 0%,#1a2d55 45%,var(--navy) 100%)}
  .poster--ask{left:607px;width:593px}

  .crest-spot{position:absolute;display:flex;flex-direction:column;align-items:center;gap:6px}
  .crest-spot .dot{border-radius:50%;background:var(--yellow)}
  .crest-spot .name{font-family:var(--body);font-weight:700;color:var(--white);font-size:13px;letter-spacing:1px}

  .title{position:absolute;font-family:var(--head);font-weight:700;color:var(--yellow);text-transform:uppercase;letter-spacing:.5px}
  .poster--ai .title{left:148px;top:18px;font-size:54px;line-height:46px}
  .tagline{position:absolute;left:148px;top:158px;font-family:var(--head);font-weight:600;color:var(--white);font-size:21px}

  /* ---------- Must do panel ---------- */
  .must-panel{position:absolute;left:17px;top:205px;width:562px;height:315px;background:var(--white);border:5px solid var(--yellow);border-radius:13px}
  .pill{position:absolute;font-family:var(--head);font-weight:700;text-transform:uppercase;font-size:21px;line-height:26px;padding-left:28px}
  .pill--must{left:14px;top:10px;width:255px;height:27px;background:var(--yellow);color:var(--navy);border-radius:4px}
  .rule{position:absolute;left:14px;display:flex;gap:11px;width:300px}
  .rule .tick{flex:none;width:44px;height:44px;border:3px solid var(--yellow);background:var(--navy);border-radius:9px;display:flex;align-items:center;justify-content:center}
  .rule h3{font-size:12.5px;font-weight:600;color:var(--navy);line-height:16px;margin-top:1px}
  .rule p{font-size:12px;color:var(--navy);line-height:16.3px}

  .ai-help{position:absolute;left:306px;top:10px;width:240px;height:288px;background:var(--navy);border-radius:6px}
  .ai-help h2{position:absolute;left:18px;top:10px;font-family:var(--head);font-weight:700;color:var(--yellow);font-size:18px;line-height:20px}
  .ai-help .sub{position:absolute;left:18px;top:32px;font-family:var(--head);font-weight:600;color:var(--yellow);font-size:12.5px}
  .help-item{position:absolute;left:14px;width:220px;display:flex;align-items:center;gap:14px}
  .help-item svg{flex:none}
  .help-item span{font-size:11.2px;font-weight:600;color:var(--white);line-height:15.5px}

  /* ---------- Cannot do panel ---------- */
  .cannot-panel{position:absolute;left:15px;top:538px;width:558px;height:205px;background:var(--grey);border-radius:14px}
  .pill--cannot{left:25px;top:8px;width:229px;height:25px;background:var(--navy);color:var(--white);border-radius:3px;font-size:19.5px;line-height:25px;padding-left:21px}
  .ban{position:absolute;top:46px;width:130px;text-align:center}
  .ban svg{display:block;margin:0 auto 8px}
  .ban p{font-size:13.5px;font-weight:500;color:var(--navy);line-height:18px}

  .footer-band{position:absolute;left:0;bottom:0;width:100%;background:var(--yellow)}
  .poster--ai .footer-band{height:89px}
  .footer-quote{position:absolute;left:63px;top:26px;font-size:14px;font-weight:600;color:var(--navy);line-height:18px}
  .footer-bulb{position:absolute;left:16px;top:20px}
  .school-mark{position:absolute;display:flex;align-items:center;gap:8px}
  .school-mark .words{font-family:var(--body);font-weight:600;color:var(--navy);text-align:center;line-height:1}
  .school-mark .words b{display:block;font-weight:600;font-size:22px;letter-spacing:1px}
  .school-mark .words small{display:block;font-weight:600;font-size:9.5px;letter-spacing:.6px;margin-top:3px}
  .school-mark .dot{width:44px;height:44px;border-radius:50%;background:var(--navy)}

  /* ---------- Ask poster ---------- */
  .poster--ask .title{left:135px;top:20px;font-size:60px;line-height:50px}
  .steps-cue{position:absolute;left:135px;top:124px;font-family:var(--head);font-weight:700;color:var(--white);font-size:29px;letter-spacing:.5px}
  .yellow-line{position:absolute;left:0;width:100%;height:4px;background:var(--yellow)}
  .divider{position:absolute;top:193px;width:1px;height:497px;background:#8a96ac}
  .step{position:absolute;top:184px;width:186px}
  .step .num{width:40px;height:40px;border-radius:50%;background:var(--yellow);color:var(--navy);font-family:var(--head);font-weight:700;font-size:27px;line-height:40px;text-align:center;margin:0 auto}
  .step .art{width:100px;height:96px;margin:10px auto 0;border-radius:10px;background:radial-gradient(circle,#31456b 0%,#142a52 70%)}
  .step h3{font-family:var(--head);font-weight:700;color:var(--white);font-size:24px;line-height:23px;text-align:center;margin-top:10px}
  .step .bar{width:36px;height:3px;background:var(--yellow);margin:13px auto 0}
  .step h4{font-size:14.8px;font-weight:700;color:var(--yellow);line-height:20px;margin-top:14px}
  .step ul{list-style:none;margin-top:6px}
  .step li{position:relative;font-size:13px;color:var(--white);line-height:21.4px;padding-left:18px;margin-bottom:3px}
  .step li::before{content:"•";position:absolute;left:2px;top:0}
  .step p.after{font-size:13px;color:var(--white);line-height:21.4px}

  .values{position:absolute;left:0;top:704px;width:100%;height:78px}
  .value{position:absolute;top:10px;display:flex;gap:12px}
  .value h5{font-size:13px;font-weight:700;color:var(--white);letter-spacing:.4px;line-height:16px}
  .value p{font-size:10.8px;color:var(--white);line-height:14.8px}
  .poster--ask .footer-band{height:65px}
  .motto{position:absolute;left:28px;top:12px;font-family:var(--script);font-size:29px;color:var(--navy)}
</style>
</head>
<body>
<div class="canvas">

  <!-- ===== Poster: Using AI responsibly ===== -->
  <section class="poster poster--ai">
    <svg class="abs" style="left:0;top:0" width="592" height="560" viewBox="0 0 592 560" aria-hidden="true">
      <path d="M592 46 C560 110 500 200 360 203" fill="none" stroke="var(--yellow-soft)" stroke-width="3"/>
      <path d="M592 40 C555 140 480 195 380 200" fill="none" stroke="var(--yellow-soft)" stroke-width="6"/>
      <path d="M0 550 C15 530 30 520 60 515" fill="none" stroke="var(--yellow-soft)" stroke-width="5"/>
    </svg>

    <div class="crest-spot" style="left:30px;top:38px">
      <div class="dot" style="width:82px;height:82px"></div>
      <div class="name">CORVAL</div>
    </div>

    <h1 class="title">Using AI and<br>other tools<br>responsibly</h1>
    <div class="tagline">Create. Learn. Think. Your way.</div>

    <div class="must-panel">
      <div class="pill pill--must">What you must do:</div>

      <div class="rule" style="top:60px">
        <div class="tick"><svg width="24" height="20" viewBox="0 0 24 20"><path d="M3 10 L10 17 L21 3" fill="none" stroke="var(--yellow)" stroke-width="3.5" stroke-linecap="round" stroke-linejoin="round"/></svg></div>
        <div><h3>Complete your own work</h3><p>Your ideas and effort show what you truly know</p></div>
      </div>
      <div class="rule" style="top:123px">
        <div class="tick"><svg width="24" height="20" viewBox="0 0 24 20"><path d="M3 10 L10 17 L21 3" fill="none" stroke="var(--yellow)" stroke-width="3.5" stroke-linecap="round" stroke-linejoin="round"/></svg></div>
        <div><h3>Demonstrate your progress</h3><p>keep drafts, notes, planning and revisions.</p></div>
      </div>
      <div class="rule" style="top:187px">
        <div class="tick"><svg width="24" height="20" viewBox="0 0 24 20"><path d="M3 10 L10 17 L21 3" fill="none" stroke="var(--yellow)" stroke-width="3.5" stroke-linecap="round" stroke-linejoin="round"/></svg></div>
        <div><h3>Use feedback to improve your work</h3><p>Feedback helps you grow and do better.</p></div>
      </div>
      <div class="rule" style="top:248px">
        <div class="tick"><svg width="24" height="20" viewBox="0 0 24 20"><path d="M3 10 L10 17 L21 3" fill="none" stroke="var(--yellow)" stroke-width="3.5" stroke-linecap="round" stroke-linejoin="round"/></svg></div>
        <div><h3>Demonstrate your understanding</h3><p>Show the ideas in your submission are your own.</p></div>
      </div>

      <div class="ai-help">
        <h2>WHAT AI CAN HELP YOU DO</h2>
        <div class="sub">(WHEN APPROVED BY YOUR TEACHER)</div>

        <div class="help-item" style="top:60px">
          <svg width="34" height="40" viewBox="0 0 34 40" fill="none" stroke="#fff" stroke-width="1.8" stroke-linecap="round"><path d="M11 26 C6 22 6 12 12 9 C18 5 28 9 27 17 C27 21 24 23 23 26 Z"/><path d="M12 30 H22 M13 33 H21 M15 36 H19"/><path d="M17 1 V4 M4 6 L6 8 M30 6 L28 8 M1 17 H4 M30 17 H33"/></svg>
          <span>Brainstrom ideas</span>
        </div>
        <div class="help-item" style="top:114px">
          <svg width="34" height="34" viewBox="0 0 34 34" fill="none" stroke="#fff" stroke-width="1.8"><path d="M30 10 A15 15 0 1 0 30 24"/><text x="6" y="21" font-family="Montserrat,Arial,sans-serif" font-size="10" font-weight="700" fill="#fff" stroke="none">ABC</text><path d="M22 24 L26 28 L33 18" stroke-linecap="round"/></svg>
          <span>Check spelling, grammer and clarity</span>
        </div>
        <div class="help-item" style="top:168px">
          <svg width="34" height="34" viewBox="0 0 34 34" fill="none" stroke="#fff" stroke-width="1.8" stroke-linejoin="round"><path d="M3 3 H31 V24 H26 L29 31 L20 24 H3 Z"/><path d="M8 10 H26 M8 15 H26 M8 20 H18" stroke-linecap="round"/></svg>
          <span>Read your work alound using text-to-speech tools</span>
        </div>
        <div class="help-item" style="top:226px">
          <svg width="34" height="36" viewBox="0 0 34 36" fill="none" stroke="#fff" stroke-width="1.8" stroke-linejoin="round"><path d="M3 18 L12 10 L18 15 L30 3 M24 3 H30 V9" stroke-linecap="round"/><path d="M4 24 H9 V34 H4 Z M13 20 H18 V34 H13 Z M22 15 H27 V34 H22 Z M1 35 H33"/></svg>
          <span>Help identify areas for improvement in a draft</span>
        </div>
      </div>
    </div>

    <div class="cannot-panel">
      <div class="pill pill--cannot">What you cannot do:</div>
      <div class="ban" style="left:6px">
        <svg width="40" height="40" viewBox="0 0 40 40"><circle cx="20" cy="20" r="19" fill="var(--red)"/><circle cx="20" cy="20" r="15" fill="none" stroke="#fff" stroke-width="2"/><path d="M13 13 L27 27 M27 13 L13 27" stroke="#fff" stroke-width="3.4" stroke-linecap="round"/></svg>
        <p>Submit AI-generated work as yor own</p>
      </div>
      <div class="ban" style="left:139px">
        <svg width="40" height="40" viewBox="0 0 40 40"><circle cx="20" cy="20" r="19" fill="var(--red)"/><circle cx="20" cy="20" r="15" fill="none" stroke="#fff" stroke-width="2"/><path d="M13 13 L27 27 M27 13 L13 27" stroke="#fff" stroke-width="3.4" stroke-linecap="round"/></svg>
        <p>Copy and paste AI responses without acknowledging or adapting them</p>
      </div>
      <div class="ban" style="left:276px">
        <svg width="40" height="40" viewBox="0 0 40 40"><circle cx="20" cy="20" r="19" fill="var(--red)"/><circle cx="20" cy="20" r="15" fill="none" stroke="#fff" stroke-width="2"/><path d="M13 13 L27 27 M27 13 L13 27" stroke="#fff" stroke-width="3.4" stroke-linecap="round"/></svg>
        <p>Use AI tools to complete the whole task for you</p>
      </div>
      <div class="ban" style="left:406px">
        <svg width="40" height="40" viewBox="0 0 40 40"><circle cx="20" cy="20" r="19" fill="var(--red)"/><circle cx="20" cy="20" r="15" fill="none" stroke="#fff" stroke-width="2"/><path d="M13 13 L27 27 M27 13 L13 27" stroke="#fff" stroke-width="3.4" stroke-linecap="round"/></svg>
        <p>Submit work that does not demonstrate your understanding</p>
      </div>
    </div>

    <footer class="footer-band">
      <svg class="footer-bulb" width="38" height="42" viewBox="0 0 38 42" fill="none" stroke="var(--navy)" stroke-width="2" stroke-linecap="round"><path d="M13 28 C8 24 8 14 14 11 C20 8 28 12 27 19 C27 23 25 25 24 28 Z"/><path d="M14 32 H24 M15 35 H23 M17 38 H21"/><path d="M19 2 V5 M6 7 L8 9 M32 7 L30 9 M2 19 H5 M33 19 H36"/></svg>
      <p class="footer-quote">If you didn’t create, develop and understand it,<br>it isn’t your work.</p>
      <div class="school-mark" style="left:405px;top:18px">
        <div class="words"><b>CORVAL</b><small>STATE HIGH SCHOOL</small></div>
        <div class="dot" style="width:50px;height:50px"></div>
      </div>
    </footer>
  </section>

  <!-- ===== Poster: Before you ask the teacher ===== -->
  <section class="poster poster--ask">
    <div class="crest-spot" style="left:30px;top:40px">
      <div class="dot" style="width:72px;height:72px"></div>
      <div class="name">CORVAL</div>
    </div>

    <h1 class="title">Before you ask<br>the teacher...</h1>
    <div class="steps-cue">TRY THESE STEPS FIRST!</div>
    <div class="yellow-line" style="top:169px"></div>

    <div class="divider" style="left:183px"></div>
    <div class="divider" style="left:377px"></div>

    <div class="step" style="left:24px">
      <div class="num">1</div>
      <div class="art" role="img" aria-label="Line illustration of a head in profile with a glowing brain"></div>
      <h3>THINK<br>FIRST</h3>
      <div class="bar"></div>
      <h4>Don’t give up<br>straight away.</h4>
      <ul>
        <li>Read the question carefully.</li>
        <li>Identify what you already know.</li>
        <li>Try a strategy you’ve used before</li>
        <li>Give yourself thinking time.</li>
      </ul>
    </div>

    <div class="step" style="left:213px">
      <div class="num">2</div>
      <div class="art" role="img" aria-label="Line illustration of a checklist clipboard with a magnifying glass"></div>
      <h3>CHECK YOUR<br>SUPPORTS</h3>
      <div class="bar"></div>
      <h4>Before asking for<br>help, check:</h4>
      <ul>
        <li>Learning goal and success criteria.</li>
        <li>Worked examples.</li>
        <li>Class notes.</li>
        <li>Classroom displays.</li>
        <li>StudyHub resources.</li>
        <li>Task sheet and instructions.</li>
      </ul>
    </div>

    <div class="step" style="left:399px">
      <div class="num">3</div>
      <div class="art" role="img" aria-label="Line illustration of three students sharing a speech bubble"></div>
      <h3>ASK 3<br>BEFORE ME</h3>
      <div class="bar"></div>
      <h4>Ask three sources<br>before asking<br>the teacher:</h4>
      <ul>
        <li>A person (partner or neighbour)</li>
        <li>A place (notes, display, StudyHub)</li>
        <li>A resource (worked example, tesk sheet)</li>
      </ul>
      <p class="after">Then ask the teacher if you till need help.</p>
    </div>

    <div class="yellow-line" style="top:699px;height:3px"></div>
    <div class="values">
      <div class="value" style="left:28px">
        <svg width="36" height="42" viewBox="0 0 36 42" fill="none" stroke="var(--yellow)" stroke-width="2.4" stroke-linejoin="round"><path d="M18 2 L33 8 V20 C33 30 26 36 18 40 C10 36 3 30 3 20 V8 Z"/><path d="M11 21 L16 26 L25 15" stroke-linecap="round"/></svg>
        <div><h5>WE BELIEVE</h5><p>In your potential<br>and your growth.</p></div>
      </div>
      <div class="value" style="left:211px">
        <svg width="42" height="42" viewBox="0 0 42 42" fill="none" stroke="#fff" stroke-width="2.2"><circle cx="19" cy="23" r="17"/><circle cx="19" cy="23" r="11"/><circle cx="19" cy="23" r="5"/><path d="M19 23 L36 6 M30 5 L36 6 L37 12" stroke="var(--yellow)" stroke-linecap="round"/></svg>
        <div><h5>WE STRIVE</h5><p>To challenge<br>and support<br>each other.</p></div>
      </div>
      <div class="value" style="left:396px">
        <svg width="46" height="42" viewBox="0 0 46 42" fill="none" stroke="var(--yellow)" stroke-width="2.2" stroke-linejoin="round"><path d="M12 3 H34 V15 C34 22 29 26 23 26 C17 26 12 22 12 15 Z"/><path d="M12 7 H4 C4 15 8 18 13 18 M34 7 H42 C42 15 38 18 33 18"/><path d="M23 26 V32 M15 38 H31 M17 33 H29 V38 H17 Z"/><path d="M23 8 L25 12 L29 12 L26 15 L27 19 L23 17 L19 19 L20 15 L17 12 L21 12 Z" stroke-width="1.4"/></svg>
        <div><h5>WE ACHIEVE</h5><p>Excellence<br>together</p></div>
      </div>
    </div>

    <footer class="footer-band">
      <div class="motto">Everyone Belong at Corval</div>
      <div class="school-mark" style="left:405px;top:9px">
        <div class="words"><b>CORVAL</b><small>STATE HIGH SCHOOL</small></div>
        <div class="dot" style="width:46px;height:46px"></div>
      </div>
    </footer>
  </section>

</div>
</body>
</html>
```